Business card

We need a business card design for our company based in Auckland , New Zealand called 'Ridge + Studio Ltd'. We provide architectural services. We would like to see designs that use the max. three colours (such as white, black, grey) The final design should communicate financial safety and growth."
Also I will provide our company logo. I would like to the logo to be embeded onto our business card.

Target Market(s)

new residential house, alteration & addition & light commericila design & drafting service

Industry/Entity Type

Architecture

Contact Information for Business Card

Company name: ridge + studio Ltd.
Name: Mark Delford
Job title: architectural designer & Design LBP
email address: mark@rplusd.co.nz
mobile number: 02 5163 2290
web site: www.rplusd.co.nz

Requirements
Must have
• My project must have..
• - embeded logo (attached company logo)
• I don't have a bigger version for our company logo, but I have one old one, so you can remove the word from it)
• - insert the attached small BKTW logo & LBP logo
• - creative, simple and clear business card.
• - Max. three colours
Nice to have
• - Here are the samples I would like to share with you: http://www.plimvora.com/blog/minimalistic-business-card-designs/
• I would like to have my business card like one of the creation.
Should not have
• TBA

```html
<!DOCTYPE html>
<html lang="en">
<head>
<meta charset="utf-8">
<title>Mark Delford – Business Card</title>
<link rel="stylesheet" href="https://fonts.googleapis.com/css2?family=Oswald:wght@700&family=Arimo:wght@400;700&display=swap">
<style>
  :root {
    --backdrop: #6e6f73;
    --card: #9e9ea0;
    --ink: #ffffff;
    --ink-soft: #f1f1f1;
  }
  * { box-sizing: border-box; margin: 0; padding: 0; }
  html, body { width: 1200px; height: 914px; overflow: hidden; }
  body {
    background: var(--backdrop);
    display: flex;
    align-items: center;
    justify-content: center;
    gap: 80px;
    font-family: "Arimo", Arial, sans-serif;
  }
  .card {
    position: relative;
    width: 340px;
    height: 556px;
    background: var(--card);
    color: var(--ink);
    box-shadow: 0 10px 28px rgba(0,0,0,0.28);
  }

  /* Front */
  .brand {
    position: absolute;
    top: 42px;
    right: 40px;
    display: flex;
    align-items: center;
    gap: 10px;
  }
  .brand-mark {
    width: 38px; height: 38px;
    border: 2px solid var(--ink);
    border-radius: 50%;
  }
  .brand-name {
    font-size: 12px;
    font-weight: 400;
    letter-spacing: 0.04em;
  }
  .identity {
    position: absolute;
    top: 340px;
    left: 40px;
    right: 30px;
  }
  .person-name {
    font-family: "Oswald", Impact, sans-serif;
    font-weight: 700;
    font-size: 34px;
    line-height: 1;
    letter-spacing: 0.01em;
    text-transform: uppercase;
  }
  .job-title {
    margin-top: 2px;
    font-size: 12px;
    font-weight: 700;
    letter-spacing: 0.01em;
  }
  .company {
    margin-top: 22px;
    font-size: 13px;
    color: var(--ink-soft);
  }
  .contact {
    margin-top: 14px;
    margin-left: 8px;
    display: grid;
    grid-template-columns: 66px auto;
    row-gap: 1px;
    font-size: 13px;
    color: var(--ink-soft);
  }
  .contact dt { font-weight: 400; }
  .contact dd { margin: 0; }

  /* Back */
  .affiliations {
    position: absolute;
    inset: 0;
    display: flex;
    flex-direction: column;
    align-items: center;
    justify-content: center;
    gap: 34px;
  }
  .association-name {
    font-family: "Oswald", Impact, sans-serif;
    font-weight: 700;
    font-size: 52px;
    line-height: 1;
    letter-spacing: 0.02em;
  }
  .licence-badge {
    width: 96px;
    height: 96px;
    border-radius: 50%;
    background: var(--ink);
    opacity: 0.92;
  }
</style>
</head>
<body>
  <section class="card card-front">
    <div class="brand">
      <span class="brand-mark"></span>
      <span class="brand-name">ridge + studio</span>
    </div>
    <div class="identity">
      <h1 class="person-name">Mark Delford</h1>
      <p class="job-title">architectural designer &amp; Design LBP</p>
      <p class="company">ridge + studio Ltd.</p>
      <dl class="contact">
        <dt>mobile</dt><dd>02 5163 2290</dd>
        <dt>email</dt><dd>mark@rplusd.co.nz</dd>
        <dt>web</dt><dd>www.rplusd.co.nz</dd>
      </dl>
    </div>
  </section>

  <section class="card card-back">
    <div class="affiliations">
      <p class="association-name">BKTW</p>
      <svg class="licence-badge" viewBox="0 0 96 96" role="img" aria-label="Licensed building practitioner badge">
        <circle cx="48" cy="48" r="48" fill="#ffffff"/>
      </svg>
    </div>
  </section>
</body>
</html>
```